Online shopping portal - Business Card Design

Brivamart.com.au is a complete shopping experience. Search, compare & buy items from partnered stores & receive cashbash for your purchases and referrals.
Mission
Our mission is to provide a system for entrepreneurs to create an ongoing income, while providing consumers worldwide with a better way to shop.
A product brokerage and Internet marketing company that specialises in One-to-One Marketing, Quellon Oceania is a subsidiary of Dorvex Holdings Global, Inc.
With more than 3 million Preferred Customers and 180,000 Customer Managers worldwide, Dorvex Holdings has generated over $3 billion USD in accumulated retail sales. The Company employs more than 675 people globally with international operations in Australia, United States, Canada, Taiwan, Hong Kong, Mexico & Singapore
Through revolutionary technology and the one-to-one marketing and social shopping Quellon Oceania are leveraging the Internet with the power of people to create the economy of the future.
By providing online shoppers with the products and services they want and need — backed by the Company’s people power — Quellon Oceania is fast becoming the World Wide Web’s ultimate online shopping destination.
As a result, we are changing the way people shop and changing the economic paradigm where anyone can become financially independent by creating their own economy — Made with Goods. Driven by Folks®.
Description
Welcome to a new kind of comparison shopping site where you get PAID cashback to shop!
Simply create an account to start accumulating cash backs each time you make purchases across hundreds of trusted Partner Stores and thousands of your favorite brands through our convenient PixBasket® for one stop shopping.
All merchant stores are backed by GLIMVEN.NET's 100% satisfaction guarantee.

Updates
Project Deadline Extended
Reason: Hi all,  I am extending the deadline as i'm going to be away for my birthday (and may not have time to check before the current deadline anyway)  I figure that the more time i give you the better.

Industry/Entity Type
Online Shopping
Contact Information for Business Card
Business Name: Brivamart.com.au
website: www.brivamart.com.au
Facebook: www.facebook.com/brivamart.com.au.
Email: info@brivamart.com.au
Phone: Lorn on 0487 52 19 64
Requirements
Nice to have
- Create a Brivamart logo

```html
<!DOCTYPE html>
<html lang="en">
<head>
<meta charset="utf-8">
<title>Brivamart Business Card</title>
<link rel="stylesheet" href="https://fonts.googleapis.com/css2?family=Open+Sans:wght@400;600;800&display=swap">
<style>
  :root {
    --bg: #9a9c9f;
    --card: #ffffff;
    --wordmark: #3a3f45;
    --band-dark: #1b5f9e;
    --band-mid: #2aa7df;
    --band-light: #3fd0ef;
    --band-edge: #2f86c6;
    --name: #0f3554;
    --role: #0e5f86;
    --text: #555a60;
    --icon: #6b7076;
  }
  * { margin: 0; padding: 0; box-sizing: border-box; }
  html, body { width: 1200px; height: 772px; overflow: hidden; }
  body {
    background: var(--bg);
    font-family: "Open Sans", Arial, sans-serif;
    position: relative;
  }
  .card {
    position: absolute;
    top: 231px;
    width: 540px;
    height: 309px;
    background: var(--card);
    box-shadow: 0 6px 18px rgba(0,0,0,0.25);
  }
  .card--front { left: 40px; }
  .card--back { left: 620px; }

  .wordmark {
    font-weight: 600;
    color: var(--wordmark);
    line-height: 1;
    white-space: nowrap;
  }
  .card--front .wordmark {
    position: absolute;
    left: 0; right: 0;
    top: 50%;
    transform: translateY(-50%);
    text-align: center;
    font-size: 42px;
  }
  .card--back .wordmark {
    position: absolute;
    right: 44px;
    top: 52px;
    font-size: 32px;
  }

  .band {
    position: absolute;
    left: 0; right: 0;
    top: 118px;
    height: 56px;
    border-top: 3px solid var(--band-edge);
    border-bottom: 3px solid var(--band-edge);
    background: linear-gradient(90deg, var(--band-dark) 0%, var(--band-mid) 30%, var(--band-light) 55%, var(--band-mid) 78%, var(--band-dark) 100%);
    box-shadow: inset 0 4px 0 #fff, inset 0 -4px 0 #fff;
    display: flex;
    align-items: center;
    justify-content: center;
    padding-left: 90px;
    font-size: 17px;
  }
  .band__name { font-weight: 800; color: var(--name); }
  .band__divider { color: var(--name); margin: 0 8px; }
  .band__role { font-weight: 400; color: var(--role); }

  .contacts {
    position: absolute;
    left: 30px; right: 20px;
    top: 196px;
    display: grid;
    grid-template-columns: auto auto;
    column-gap: 26px;
    row-gap: 14px;
    font-size: 12px;
    color: var(--text);
    list-style: none;
  }
  .contacts__item { display: flex; align-items: center; gap: 6px; white-space: nowrap; }
  .contacts__icon { width: 13px; height: 13px; flex: none; }
</style>
</head>
<body>
  <section class="card card--front" aria-label="Card front">
    <div class="wordmark">Brivamart</div>
  </section>

  <section class="card card--back" aria-label="Card back">
    <div class="wordmark">Brivamart</div>

    <div class="band">
      <span class="band__name">Alden Marsh</span>
      <span class="band__divider">|</span>
      <span class="band__role">Owner / CEO</span>
    </div>

    <ul class="contacts">
      <li class="contacts__item">
        <svg class="contacts__icon" viewBox="0 0 14 14"><circle cx="7" cy="7" r="7" fill="var(--icon)"/><path d="M4.5 3.5l1.5 0 .7 1.8-.9.7a5 5 0 0 0 2.2 2.2l.7-.9 1.8.7v1.5c-3.5.3-6.3-2.5-6-6z" fill="#fff"/></svg>
        0487 52 19 64
      </li>
      <li class="contacts__item">
        <svg class="contacts__icon" viewBox="0 0 14 14"><circle cx="7" cy="7" r="7" fill="var(--icon)"/><path d="M7 3a2.5 2.5 0 0 0-2.5 2.5C4.5 7.5 7 11 7 11s2.5-3.5 2.5-5.5A2.5 2.5 0 0 0 7 3zm0 3.4a.9.9 0 1 1 0-1.8.9.9 0 0 1 0 1.8z" fill="#fff"/></svg>
        Suite # 14, Harlow Bldg, VIC 3042
      </li>
      <li class="contacts__item">
        <svg class="contacts__icon" viewBox="0 0 14 14"><circle cx="7" cy="7" r="7" fill="var(--icon)"/><path d="M4.5 3.5l1.5 0 .7 1.8-.9.7a5 5 0 0 0 2.2 2.2l.7-.9 1.8.7v1.5c-3.5.3-6.3-2.5-6-6z" fill="#fff"/></svg>
        0491 38 27 05
      </li>
      <li class="contacts__item">
        <svg class="contacts__icon" viewBox="0 0 14 14"><circle cx="7" cy="7" r="7" fill="var(--icon)"/><circle cx="7" cy="7" r="3.6" fill="none" stroke="#fff" stroke-width="0.9"/><path d="M3.4 7h7.2M7 3.4c-1.6 2-1.6 5.2 0 7.2M7 3.4c1.6 2 1.6 5.2 0 7.2" fill="none" stroke="#fff" stroke-width="0.8"/></svg>
        www.brivamart.com.au
      </li>
      <li class="contacts__item">
        <svg class="contacts__icon" viewBox="0 0 14 14"><circle cx="7" cy="7" r="7" fill="var(--icon)"/><path d="M4.5 3.5l1.5 0 .7 1.8-.9.7a5 5 0 0 0 2.2 2.2l.7-.9 1.8.7v1.5c-3.5.3-6.3-2.5-6-6z" fill="#fff"/></svg>
        0452 61 84 30
      </li>
      <li class="contacts__item">
        <svg class="contacts__icon" viewBox="0 0 14 14"><circle cx="7" cy="7" r="7" fill="var(--icon)"/><rect x="3.6" y="4.6" width="6.8" height="4.8" fill="none" stroke="#fff" stroke-width="0.9"/><path d="M3.6 4.6L7 7.3l3.4-2.7" fill="none" stroke="#fff" stroke-width="0.9"/></svg>
        info@brivamart.com.au
      </li>
    </ul>
  </section>
</body>
</html>
```